HOT TUB - SPAS service needs an business card

I need an business for my company who his specialise in a maintenance,water treatment and cleaning of Hot Tub - Spas for commercial and residential customers. The company operate mainly in the ski resort of Chamonix, Megève and St Gervais. The final product should communicate pure water, cleanest and professional for luxury property's.
I have upload a logo but any improvement on it is welcome.(color,size, details etc..) or any other idea. Thank you
Company Name: 58 BAINS
My name: Lucien Marchetti
Email: lucimarch@examplemail.net
Tel: +33 (0)6 71 58 29 64
Description to be on the card in french(first langage) and in English:
- Spas service
- Entretien, traitement eau, nettoyage.
- Maintenance, water treatment, cleaning.
Industry/Entity Type
Residential
Colors
Designer to choose colors to be used in the design.
Look and feel
Each slider illustrates characteristics of the customer's brand and the style your logo design should communicate.

```html
<!DOCTYPE html>
<html lang="fr">
<head>
<meta charset="utf-8">
<title>58 BAINS – Spas service</title>
<link rel="stylesheet" href="https://fonts.googleapis.com/css2?family=Roboto:ital,wght@1,400;1,700&display=swap">
<style>
  :root {
    --ink-white: #f2f4f7;
    --ink-soft: #dde2e9;
    --photo-dark: #141b24;
    --deck-dark: #1e2631;
    --deck-mid: #3b4654;
    --tub-mid: #5c6877;
    --tub-light: #a9b4c1;
    --panel-shade: rgba(6, 9, 14, 0.74);
    --band-shade: rgba(8, 10, 14, 0.84);
    --rule: rgba(200, 210, 222, 0.45);
  }
  * { margin: 0; padding: 0; box-sizing: border-box; }
  html, body {
    width: 1200px;
    height: 686px;
    overflow: hidden;
    background: var(--photo-dark);
  }
  .card {
    position: relative;
    width: 1200px;
    height: 686px;
    overflow: hidden;
    font-family: "Roboto", "Arial", sans-serif;
    font-style: italic;
    color: var(--ink-white);
  }
  .hero-photo {
    position: absolute;
    inset: 0;
    background:
      radial-gradient(ellipse 62% 34% at 60% 64%, var(--tub-light) 0%, var(--tub-mid) 42%, rgba(60, 70, 84, 0.6) 70%, transparent 88%),
      radial-gradient(ellipse 40% 22% at 86% 36%, rgba(190, 200, 212, 0.35) 0%, transparent 100%),
      linear-gradient(180deg, var(--deck-dark) 0%, var(--deck-mid) 30%, #4d5866 48%, #3a4450 78%, #252d37 100%);
  }
  .contact-panel {
    position: absolute;
    left: 80px;
    top: 0;
    width: 312px;
    height: 686px;
    background: var(--panel-shade);
    border-left: 1px solid var(--rule);
    border-right: 1px solid var(--rule);
  }
  .contact-title {
    position: absolute;
    left: 133px;
    top: 60px;
    font-size: 20px;
    font-weight: 700;
    letter-spacing: 1.5px;
    text-decoration: underline;
    text-underline-offset: 3px;
  }
  .contact-block {
    position: absolute;
    left: 133px;
    list-style: none;
    font-size: 17px;
    font-weight: 400;
    line-height: 37.7px;
    color: var(--ink-soft);
    white-space: nowrap;
  }
  .contact-block--services { top: 112px; }
  .contact-block--direct { top: 349px; }
  .contact-block a {
    color: var(--ink-white);
    text-decoration: underline;
    text-underline-offset: 3px;
  }
  .area-band {
    position: absolute;
    left: 0;
    top: 570px;
    width: 1200px;
    height: 58px;
    background: var(--band-shade);
    border-bottom: 1px solid var(--rule);
  }
  .area-note {
    position: absolute;
    right: 120px;
    top: 589px;
    font-size: 15px;
    color: var(--ink-white);
    letter-spacing: 0.2px;
    white-space: nowrap;
  }
</style>
</head>
<body>
  <div class="card">
    <div class="hero-photo" role="img" aria-label="Photograph of a round outdoor hot tub on a wooden chalet terrace with railings and a snowy mountain village behind, in cool blue-grey tones"></div>

    <div class="contact-panel"></div>

    <h2 class="contact-title">CONTACT US:</h2>

    <ul class="contact-block contact-block--services">
      <li>Spas service</li>
      <li>Entretien, traitement eau,</li>
      <li>nettoyage.</li>
      <li>Maintenance, water treatment,</li>
      <li>cleaning.</li>
    </ul>

    <ul class="contact-block contact-block--direct">
      <li>58 BAINS</li>
      <li>Lucien Marchetti</li>
      <li>lucimarch@examplemail.net</li>
      <li>call: +33 (0)6 71 58 29 64</li>
      <li><a href="#">website: www.58bains-spas.fr</a></li>
    </ul>

    <div class="area-band"></div>
    <p class="area-note">The company operate mainly in the ski resort of Chamonix, Megève and St Gervais.</p>
  </div>
</body>
</html>
```